Tallowmere Cornerstones

Need to improve polish and professionalism of PPT presentation. Get consistent look and feel through whole slides, improved look and feel while maintaining the corporate standards/colour scheme, from the Brackwyn corporate presentation. Need everything in Arial font with colours consistent with the PPT template

```html
<!DOCTYPE html>
<html lang="en">
<head>
<meta charset="utf-8">
<title>Tallowmere Cornerstones – KPIs &amp; Production Fundamentals</title>
<link href="https://fonts.googleapis.com/css2?family=Arimo:wght@400;700&display=swap" rel="stylesheet">
<style>
  :root{
    --ink:#0d2b33;
    --canvas:#0d2930;
    --red:#d32a2e;
    --table-red:#c00000;
    --yellow:#ffff00;
    --grey-text:#555b5e;
    --light:#ffffff;
    --icon-grey:#d9d9d9;
  }
  *{box-sizing:border-box;margin:0;padding:0}
  html,body{width:1011px;height:1200px;overflow:hidden;background:var(--canvas);font-family:'Arimo',Arial,sans-serif;color:var(--ink)}
  .slide{position:absolute;width:832px;height:468px;background:var(--light);overflow:hidden;transform:scale(.5733);transform-origin:0 0}
  .abs{position:absolute}
  .accent-rule{position:absolute;top:25px;width:56px;height:2px;background:var(--red)}
  .accent-rule.center{left:388px}
  .slide-title{position:absolute;left:0;right:0;top:38px;text-align:center;font-size:30px;font-weight:700;color:var(--ink)}
  .slide-sub{position:absolute;left:0;right:0;top:88px;text-align:center;font-size:17px;color:var(--ink)}
  .footer-logo{position:absolute;left:22px;top:433px;font-size:25px;font-weight:700;letter-spacing:1px;color:var(--ink)}
  .footer-bar{position:absolute;left:185px;right:0;top:436px;height:28px;background:var(--red);color:#fff;font-size:13px;display:flex;align-items:center;justify-content:space-between;padding:0 27px 0 113px}
  /* cover */
  .cover-photo{position:absolute;inset:0;background:linear-gradient(90deg,#efefee 0%,#e6e4e0 38%,#b9ab8f 55%,#8b7448 70%,#6e5a3b 85%,#4f4536 100%)}
  .cover-logo{left:50px;top:82px;font-size:46px;font-weight:700;letter-spacing:2px}
  .cover-title{left:50px;top:176px;font-size:30px;font-weight:700;line-height:45px}
  .cover-body{left:50px;top:282px;width:520px;font-size:13px;line-height:22px}
  .cover-date{left:50px;top:437px;font-size:13px}
  .cover-copy{left:580px;top:436px;font-size:13px}
  /* objectives */
  .obj-title{left:22px;top:44px;font-size:30px;font-weight:700;line-height:37px}
  .obj-note{left:353px;top:47px;font-size:11.5px;line-height:22px;width:440px}
  .obj-head{top:128px;font-size:17px;font-weight:700;line-height:22px;text-transform:uppercase}
  .step-label{font-size:15px;font-weight:700;line-height:22px;text-transform:uppercase}
  /* pills */
  .pill-dark{position:absolute;background:var(--ink);color:#fff;border-radius:30px;display:flex;align-items:center;justify-content:center;font-size:19px}
  .pill-outline{position:absolute;border:2px solid var(--ink);border-radius:40px;display:flex;align-items:center;font-size:19px;line-height:22px}
  .bullets{list-style:none}
  .bullets li{position:relative;padding-left:20px}
  .bullets li::before{content:"✦";position:absolute;left:0;color:var(--red);font-size:.8em}
  .hl{color:var(--red);font-weight:700}
  /* time usage table */
  .tum{position:absolute;left:40px;top:98px;width:768px;display:grid;grid-template-columns:repeat(6,128px);grid-template-rows:30px 32px 30px 32px;color:#fff;font-weight:700;font-size:12px;text-align:center}
  .tum div{display:flex;align-items:center;justify-content:center;border:1px solid #fff;background:var(--ink)}
  .tum .down{background:var(--table-red)}
  .tum .standby{background:var(--yellow);color:var(--ink)}
  .tum .big{font-size:13.5px}
</style>
</head>
<body>

<!-- Cover -->
<section class="slide" style="left:16px;top:23.5px">
  <div class="cover-photo" role="img" aria-label="Photograph of a large yellow mining haul truck loaded with ore in an open-pit mine"></div>
  <div class="abs cover-logo">BRACKWYN</div>
  <div class="abs cover-title">Tallowmere Cornerstones<br>KPIs &amp; Production Fundamentals</div>
  <p class="abs cover-body">Sed ut perspiciatis unde omnis iste natus error sit voluptatem accusantium doloremque laudantium, totam rem aperiam, eaque ipsa quae ab illo inventore veritatis et quasi architecto beatae vitae dicta sunt explicabo.</p>
  <div class="abs cover-date">Nov 2024</div>
  <div class="abs cover-copy">© 2024 Brackwyn. All Rights Reserved</div>
</section>

<!-- Objectives -->
<section class="slide" style="left:510px;top:24px">
  <div class="accent-rule" style="left:22px"></div>
  <h1 class="abs obj-title">KPI &amp; Production<br>Fundamentals</h1>
  <p class="abs obj-note">The goal will be to create a baseline of understanding and a common language across the entire mine-ops team You may already understand these concepts<br>This is the time to ask questions and get clarification!</p>
  <div class="abs obj-head" style="left:22px">At the end of this module,<br>you will understand</div>
  <div class="abs obj-head" style="left:357px">Understand the key concepts of mine<br>production KPIs</div>
  <svg class="abs" style="left:0;top:0" width="832" height="420" viewBox="0 0 832 420">
    <polyline points="55,273 212,227 369,273 526,227 683,273" fill="none" stroke="var(--red)" stroke-width="1" stroke-dasharray="3 3"/>
    <g fill="var(--red)">
      <circle cx="55" cy="273" r="20"/><circle cx="212" cy="227" r="20"/><circle cx="369" cy="273" r="20"/><circle cx="526" cy="227" r="20"/><circle cx="683" cy="273" r="20"/>
    </g>
    <g fill="none" stroke="#fff" stroke-width="1.5">
      <g transform="translate(55,273)"><circle cx="-4" cy="-4" r="5"/><path d="M-1 4v4M3 2v6M7 -1v9M-8 8h17"/></g>
      <g transform="translate(212,227)"><circle cx="-4" cy="-4" r="5"/><path d="M-1 4v4M3 2v6M7 -1v9M-8 8h17"/></g>
      <g transform="translate(369,273)"><circle cx="-4" cy="-4" r="5"/><path d="M-1 4v4M3 2v6M7 -1v9M-8 8h17"/></g>
      <g transform="translate(526,227)"><circle cx="-4" cy="-4" r="5"/><path d="M-1 4v4M3 2v6M7 -1v9M-8 8h17"/></g>
      <g transform="translate(683,273)"><circle cx="-4" cy="-4" r="5"/><path d="M-1 4v4M3 2v6M7 -1v9M-8 8h17"/></g>
    </g>
  </svg>
  <div class="abs step-label" style="left:37px;top:306px">Time usage<br>model</div>
  <div class="abs step-label" style="left:194px;top:260px">Availability,<br>utilization and<br>productivity</div>
  <div class="abs step-label" style="left:351px;top:306px">Elements of<br>the haul<br>cycle</div>
  <div class="abs step-label" style="left:508px;top:260px">Elements of<br>the loading<br>cycle</div>
  <div class="abs step-label" style="left:665px;top:306px">How changes in<br>each of these<br>elements<br>impact mine<br>production</div>
  <div class="footer-logo" style="top:431px">BRACKWYN</div>
  <div class="footer-bar" style="top:436px"><span>© 2024 Brackwyn. All Rights Reserved</span><span>Page No:02</span></div>
</section>

<!-- What makes up production (1) -->
<section class="slide" style="left:16px;top:313px">
  <div class="accent-rule center"></div>
  <h2 class="slide-title">What Makes up Production</h2>
  <p class="slide-sub">In its simplest terms, we calculate production like this:</p>
  <svg class="abs" style="left:0;top:0" width="832" height="320">
    <path d="M416 194 v20 l-14 10" stroke="#999" stroke-dasharray="2 3" fill="none"/>
  </svg>
  <div class="pill-dark" style="left:324px;top:135px;width:184px;height:59px">Production</div>
  <div class="pill-outline" style="left:179px;top:223px;width:238px;height:72px;padding-left:42px">Equipment<br>Productivity</div>
  <div class="pill-outline" style="left:417px;top:223px;width:236px;height:72px;padding-left:88px">Operating<br>Time</div>
  <svg class="abs" style="left:340px;top:218px" width="150" height="82" viewBox="0 0 150 82">
    <circle cx="41" cy="41" r="34" fill="#fff"/><circle cx="41" cy="41" r="28" fill="var(--icon-grey)"/>
    <path d="M41 7 A34 34 0 0 1 41 75" stroke="var(--red)" stroke-width="3" fill="none"/>
    <rect x="29" y="31" width="24" height="17" fill="none" stroke="#333" stroke-width="2"/><path d="M36 53h10M41 48v5" stroke="#333" stroke-width="2"/>
    <circle cx="111" cy="41" r="34" fill="#fff"/><circle cx="111" cy="41" r="28" fill="var(--icon-grey)"/>
    <path d="M111 7 A34 34 0 0 0 111 75" stroke="var(--red)" stroke-width="3" fill="none"/>
    <circle cx="111" cy="41" r="13" fill="none" stroke="#333" stroke-width="2"/><path d="M111 33v8l6 4" stroke="#333" stroke-width="2" fill="none"/>
  </svg>
  <p class="abs" style="left:0;right:0;top:316px;text-align:center;font-size:19px">This is true for any process</p>
  <p class="abs" style="left:0;right:0;top:353px;text-align:center;font-size:15px"><span class="hl" style="font-weight:400">✦</span> Mowing the lawn &nbsp;&nbsp; <span class="hl" style="font-weight:400">✦</span>DrivingMine &nbsp;&nbsp; <span class="hl" style="font-weight:400">✦</span> Production</p>
  <p class="abs" style="left:0;right:0;top:390px;text-align:center;font-size:18px">Production goes up or down because of a change in <span class="hl">Equipment Productivity</span> or <span class="hl">Operating Time</span></p>
  <div class="footer-logo">BRACKWYN</div>
  <div class="footer-bar"><span>© 2024 Brackwyn. All Rights Reserved</span><span>Page No:03</span></div>
</section>

<!-- What makes up production (2) -->
<section class="slide" style="left:510px;top:313px">
  <div class="accent-rule center"></div>
  <h2 class="slide-title">What Makes up Production</h2>
  <p class="slide-sub">In its simplest terms, we calculate production like this:</p>
  <svg class="abs" style="left:0;top:0" width="832" height="260">
    <path d="M324 165 L300 200 M508 165 L535 205" stroke="#999" stroke-dasharray="2 3" fill="none"/>
  </svg>
  <div class="pill-dark" style="left:324px;top:135px;width:184px;height:59px">Production</div>
  <div class="pill-outline" style="left:67px;top:187px;width:238px;height:72px;padding-left:42px">Equipment<br>Productivity</div>
  <div class="pill-outline" style="left:533px;top:187px;width:238px;height:72px;padding-left:90px">Operating<br>Time</div>
  <svg class="abs" style="left:228px;top:182px" width="82" height="82" viewBox="0 0 82 82">
    <circle cx="41" cy="41" r="34" fill="#fff"/><circle cx="41" cy="41" r="28" fill="var(--icon-grey)"/>
    <path d="M41 7 A34 34 0 0 1 41 75" stroke="var(--red)" stroke-width="3" fill="none"/>
    <rect x="29" y="31" width="24" height="17" fill="none" stroke="#333" stroke-width="2"/><path d="M36 53h10M41 48v5" stroke="#333" stroke-width="2"/>
  </svg>
  <svg class="abs" style="left:529px;top:184px" width="82" height="82" viewBox="0 0 82 82">
    <circle cx="41" cy="41" r="34" fill="#fff"/><circle cx="41" cy="41" r="28" fill="var(--icon-grey)"/>
    <path d="M41 7 A34 34 0 0 0 41 75" stroke="var(--red)" stroke-width="3" fill="none"/>
    <circle cx="41" cy="41" r="13" fill="none" stroke="#333" stroke-width="2"/><path d="M41 33v8l6 4" stroke="#333" stroke-width="2" fill="none"/>
  </svg>
  <ul class="bullets abs" style="left:88px;top:292px;width:700px;font-size:13px;line-height:22px;color:var(--grey-text)">
    <li>Operating time is the time when a piece of equipment is performing it's primary function</li>
    <li>To better understand, communicate and discuss the different categories of how we calculate operating time, we use something called a Time Usage Model</li>
    <li>Each industry has its own time usage model, and they can vary slightly from industry to industry</li>
    <li>Even within an industry, (e.g. Mining) a Time Usage Model can vary from operation to operation</li>
  </ul>
  <div class="footer-logo">BRACKWYN</div>
  <div class="footer-bar"><span>© 2024 Brackwyn. All Rights Reserved</span><span>Page No:04</span></div>
</section>

<!-- Generic TUM -->
<section class="slide" style="left:15.5px;top:604px">
  <div class="accent-rule center"></div>
  <h2 class="slide-title">Generic Time Usage Model</h2>
  <div class="tum">
    <div class="big" style="grid-column:1/7">Calendar Time</div>
    <div class="big" style="grid-column:1/5">Available Time</div>
    <div class="big down" style="grid-column:5/7">Down</div>
    <div class="big" style="grid-column:1/3">Operating Time</div>
    <div style="grid-column:3/4;grid-row:3/5">Operating Delay</div>
    <div class="standby" style="grid-column:4/5;grid-row:3/5">Stand By Time</div>
    <div class="down" style="grid-column:5/6;grid-row:3/5">Unscheduled</div>
    <div class="down" style="grid-column:6/7;grid-row:3/5">Scheduled</div>
    <div>Effective Time</div>
    <div>Non-Effective Time</div>
  </div>
  <ul class="bullets abs" style="left:52px;top:254px;width:720px;font-size:18px;line-height:31px;color:var(--grey-text)">
    <li>This is a generic Mining time usage model</li>
    <li>There may be variations from mine-to-mine (ie Utilized time vs Operating Time) but this model describes everything mine operations needs to know about the time usage of a piece of equipment</li>
  </ul>
  <div class="footer-logo">BRACKWYN</div>
  <div class="footer-bar"><span>© 2024 Brackwyn. All Rights Reserved</span><span>Page No:05</span></div>
</section>

<!-- TUM effective time -->
<section class="slide" style="left:510px;top:604px">
  <div class="accent-rule center"></div>
  <h2 class="slide-title">TUM – Effective Time</h2>
  <div class="tum">
    <div class="big" style="grid-column:1/7">Calendar Time</div>
    <div class="big" style="grid-column:1/5">Available Time</div>
    <div class="big down" style="grid-column:5/7">Down</div>
    <div class="big" style="grid-column:1/3">Operating Time</div>
    <div style="grid-column:3/4;grid-row:3/5">Operating Delay</div>
    <div class="standby" style="grid-column:4/5;grid-row:3/5">Stand By Time</div>
    <div class="down" style="grid-column:5/6;grid-row:3/5">Unscheduled</div>
    <div class="down" style="grid-column:6/7;grid-row:3/5">Scheduled</div>
    <div>Effective Time</div>
    <div>Non-Effective Time</div>
  </div>
  <ul class="bullets abs" style="left:30px;top:256px;width:780px;font-size:18px;font-weight:700;line-height:24px">
    <li>Effective Time is the time when the equipment is doing its productive activities
      <div style="font-size:12px;font-weight:400;line-height:21px;color:var(--grey-text)">It excludes waiting/idle time that is included in operating time<br>This waiting/idle, non-effective time is a part of the regular operation of the machine, but is not productive</div>
      <ul class="bullets" style="font-size:9px;line-height:15px;margin-bottom:8px">
        <li style="padding-left:12px">Shovel Hang</li>
        <li style="padding-left:12px">Truck wait @ dump or wait @ shovel</li>
      </ul>
    </li>
    <li style="margin-bottom:12px">Effective Utilization % = Effective Time / Available Time</li>
    <li>OEE % = Effective Time / Calendar Time</li>
  </ul>
  <div class="footer-logo">BRACKWYN</div>
  <div class="footer-bar"><span>© 2024 Brackwyn. All Rights Reserved</span><span>Page No:06</span></div>
</section>

<!-- Haul truck productivity -->
<section class="slide" style="left:15.5px;top:897px">
  <div class="accent-rule center"></div>
  <h2 class="slide-title">Equipment Productivity – Haul Trucks</h2>
  <svg class="abs" style="left:0;top:0" width="540" height="380" viewBox="0 0 540 380" font-family="Arimo, Arial, sans-serif">
    <defs>
      <linearGradient id="tailFade" x1="0" x2="1" y1="0" y2="0">
        <stop offset="0" stop-color="#555"/><stop offset=".2" stop-color="#bbb"/><stop offset="1" stop-color="#eee"/>
      </linearGradient>
    </defs>
    <rect x="61" y="113" width="425" height="199" fill="none" stroke="#222" stroke-width="1.5"/>
    <path d="M61,310 L87.5,306.1 L114.1,297.3 L140.2,279.7 L166.7,250.9 L193.3,211.3 L219.9,168.4 L246.4,134.2 L273,121 L299.6,134.2 L326.1,168.4 L352.7,211.3 L379.3,250.9 L379.3,312 L61,312 Z" fill="#555"/>
    <path d="M379.3,250.9 L405.8,279.7 L432.4,297.3 L458.9,306.1 L485.5,310 L485.5,312 L379.3,312 Z" fill="url(#tailFade)"/>
    <path d="M273 121V312M379.3 250V312" stroke="#000" stroke-width="1.5"/>
    <line x1="61" y1="312" x2="486" y2="312" stroke="#000" stroke-width="2"/>
    <polygon points="120,222 160,186 160,208 273,208 273,236 160,236 160,258" fill="#d0d0d0" stroke="#888"/>
    <text x="210" y="231" fill="#fff" font-size="22" font-weight="700" text-anchor="middle">50 %</text>
    <rect x="45" y="133" width="33" height="152" fill="#666" stroke="#222"/>
    <text transform="translate(68,209) rotate(-90)" fill="#fff" font-size="20" font-weight="700" text-anchor="middle">Productivity</text>
    <rect x="363" y="133" width="35" height="109" fill="#666" stroke="#222"/>
    <text transform="translate(388,187) rotate(-90)" fill="#fff" font-size="20" font-weight="700" text-anchor="middle">Durability</text>
    <rect x="470" y="133" width="34" height="120" fill="#ddd" stroke="#222"/>
    <text transform="translate(494,193) rotate(-90)" fill="#000" font-size="20" font-weight="700" text-anchor="middle">Tested Limit</text>
    <text x="440" y="291" font-size="22" font-weight="700" text-anchor="middle">10%</text>
    <text transform="translate(28,212) rotate(-90)" font-size="11" text-anchor="middle">Number of Loads</text>
    <g font-size="9" text-anchor="middle">
      <text x="61" y="331">80</text><text x="114" y="331">85</text><text x="167" y="331">90</text><text x="220" y="331">95</text><text x="273" y="331">100</text><text x="326" y="331">105</text><text x="379" y="331">110</text><text x="432" y="331">115</text><text x="486" y="331">120</text>
    </g>
    <text x="273" y="356" font-size="12" text-anchor="middle">% of Target Payload</text>
  </svg>
  <ul class="bullets abs" style="left:528px;top:128px;width:270px;font-size:15px;font-weight:700;line-height:22px">
    <li style="margin-bottom:22px">To increase productivity, we want to maximize truck payload while adhering to the 10/10/20</li>
    <li style="margin-bottom:22px">No more than 10% of loads between 110% and 120% of Nominal Payload</li>
    <li>No loads greater than 120% of Nominal Payload</li>
  </ul>
  <div class="footer-logo">BRACKWYN</div>
  <div class="footer-bar"><span>© 2024 Brackwyn. All Rights Reserved</span><span>Page No:07</span></div>
</section>

<!-- Visual management -->
<section class="slide" style="left:512.5px;top:897px">
  <div class="accent-rule center"></div>
  <h2 class="slide-title">Visual Management – Process</h2>
  <ul class="bullets abs" style="left:46px;top:105px;width:740px;font-size:15px;line-height:30.5px">
    <li style="font-weight:700">Visual Management Meeting - &nbsp;5:00 AM, 12:00 PM and 5:00 PM</li>
    <li>The goal is for the meeting to take 10 minutes only</li>
    <li>Attendees should come prepared</li>
    <li>Understand the operating scenario – over-trucked or</li>
    <li>under-trucked, crusher status, etc. What strategies should be</li>
    <li>employed based on the operations playbook</li>
    <li>Review Visual Management Slides in Order</li>
    <li>Review red KPIs, move past green ones</li>
    <li>Not a deep dive or time to investigate SIC trends</li>
    <li>Focus on identifying issues and taking action</li>
  </ul>
  <div class="footer-logo">BRACKWYN</div>
  <div class="footer-bar"><span>© 2024 Brackwyn. All Rights Reserved</span><span>Page No:08</span></div>
</section>

</body>
</html>
```